Kestrel Ridge Business Card Design

Design new, 2 sides, business cards for a residential and light commercial heating, air conditioning contractor.

Target Market(s)

Homeowners, small businesses

Industry/Entity Type

Business

Contact Information for Business Card

Dominic Westerhall
Phone - 862-415-2736
Email
Address - PO box 518
Brightwater NJ 07912
Website - www.HarborBreezeLLC.example

Requirements
Must have
• logo, company colors, standard size with no die cut, so I can use nova stamp

```html
<!DOCTYPE html>
<html lang="en">
<head>
<meta charset="utf-8">
<title>Kestrel Ridge Business Card</title>
<link href="https://fonts.googleapis.com/css2?family=Open+Sans:wght@400;600;700&display=swap" rel="stylesheet">
<style>
  :root {
    --canvas: #e9e6e3;
    --card-white: #ffffff;
    --brand-red: #9b1f32;
    --brand-orange: #f08a2b;
    --text-light: #ffffff;
  }
  * { box-sizing: border-box; margin: 0; padding: 0; }
  html, body { width: 1200px; height: 900px; overflow: hidden; }
  body {
    position: relative;
    background: var(--canvas);
    font-family: "Open Sans", Arial, sans-serif;
  }
  .card {
    position: absolute;
    background: var(--card-white);
    overflow: hidden;
    box-shadow: 0 6px 18px rgba(0,0,0,0.18);
  }
  /* Front card */
  .card-front { left: 78px; top: 35px; width: 587px; height: 362px; }
  .front-band {
    position: absolute; left: 0; right: 0; top: 143px; bottom: 0;
    background: var(--brand-red);
  }
  .brand-name {
    position: absolute;
    font-weight: 700;
    white-space: nowrap;
    color: var(--brand-red);
    text-align: center;
    line-height: 1;
  }
  .card-front .brand-name { left: 245px; width: 315px; top: 68px; font-size: 38px; }
  .contact-block { position: absolute; left: 31px; top: 150px; color: var(--text-light); }
  .person-name { font-size: 20px; font-weight: 600; line-height: 1.3; }
  .person-title { font-size: 15px; line-height: 1.3; margin-bottom: 16px; }
  .contact-list { list-style: none; }
  .contact-list li {
    display: flex; align-items: center; gap: 9px;
    font-size: 15px; height: 24.5px;
  }
  .contact-list svg { width: 12px; height: 12px; fill: var(--text-light); flex: none; }
  .address {
    position: absolute; left: 31px; bottom: 16px;
    color: var(--text-light); font-size: 15px;
  }
  /* Back card */
  .card-back { left: 388px; top: 505px; width: 567px; height: 352px; }
  .back-band {
    position: absolute; left: 0; right: 0; top: 110px; height: 130px;
    background: var(--brand-orange);
  }
  .card-back .brand-name {
    left: 0; right: 0; top: 152px; font-size: 44px;
  }
</style>
</head>
<body>
  <section class="card card-front">
    <div class="front-band"></div>
    <div class="brand-name">Kestrel Ridge</div>
    <div class="contact-block">
      <div class="person-name">Dominic Westerhall</div>
      <div class="person-title">Managing Director</div>
      <ul class="contact-list">
        <li>
          <svg viewBox="0 0 24 24" aria-hidden="true"><path d="M6.6 10.8a15.1 15.1 0 0 0 6.6 6.6l2.2-2.2c.3-.3.7-.4 1-.2 1.1.4 2.3.6 3.6.6.6 0 1 .4 1 1V20c0 .6-.4 1-1 1A17 17 0 0 1 3 4c0-.6.4-1 1-1h3.5c.6 0 1 .4 1 1 0 1.3.2 2.5.6 3.6.1.3 0 .7-.2 1z"/></svg>
          (862)-415-2736
        </li>
        <li>
          <svg viewBox="0 0 24 24" aria-hidden="true"><path d="M6 2h9l3 3v5h2a2 2 0 0 1 2 2v8a2 2 0 0 1-2 2H4a2 2 0 0 1-2-2v-8a2 2 0 0 1 2-2h2zm2 2v6h8V6h-2V4zm-3 9v2h3v-2zm5 0v2h3v-2zm5 0v2h3v-2zm-10 4v2h3v-2zm5 0v2h3v-2zm5 0v2h3v-2z"/></svg>
          862-415-2790
        </li>
        <li>
          <svg viewBox="0 0 24 24" aria-hidden="true"><path d="M2 5h20v14H2zm2 2v.5l8 5 8-5V7zm0 3v7h16v-7l-8 5z"/></svg>
          info@kestrelridge.example
        </li>
        <li>
          <svg viewBox="0 0 24 24" aria-hidden="true"><path d="M12 2a10 10 0 1 0 0 20 10 10 0 0 0 0-20zm-1 17.9A8 8 0 0 1 4.1 10L9 15v1a2 2 0 0 0 2 2zm6.9-2.5A2 2 0 0 0 16 16h-1v-3a1 1 0 0 0-1-1H8v-2h2a1 1 0 0 0 1-1V7h2a2 2 0 0 0 2-2v-.4a8 8 0 0 1 2.9 12.8z"/></svg>
          www.KestrelRidgeLLC.example
        </li>
      </ul>
    </div>
    <div class="address">PO box 518, Brightwater NJ 07912</div>
  </section>

  <section class="card card-back">
    <div class="back-band"></div>
    <div class="brand-name">Kestrel Ridge</div>
  </section>
</body>
</html>
```